Banner ads for LP that work with same theme as below banners

Love the banner ads below. Need more with attached photos. But use the same wording, font as in below banner ads. Should be LP size 1200/627 so I can use for Pixorly and LP. Looking for great ads to use as LP ads. We do lots of ads so it will be worth your time to enter this contest you will be rewarded with a ton of work. Need several banner ads that work together. So maybe 1 of the dresses, 1 of the sweater, 1 of the leggings, 1 of the jacket

Target Market(s)

Women 24-45

Industry/Entity Type

Fashion

Requirements
Must have
• Banner ads that work for LP and Pixorly
Nice to have
• Several options to choose from
Should not have
• not sure

```html
<!DOCTYPE html>
<html lang="en">
<head>
<meta charset="utf-8">
<title>New Winter Collection</title>
<link rel="stylesheet" href="https://fonts.googleapis.com/css2?family=Cinzel:wght@700&family=Cookie&family=Open+Sans:wght@400;700&display=swap">
<style>
  :root {
    --edge-blue: #8fa3d6;
    --edge-lavender: #b7bfe6;
    --centre-white: #f4f4f6;
    --mist: #dfe1ea;
    --band: #f3f3f3;
    --ink: #111111;
    --script-white: #ffffff;
    --script-shadow: rgba(60, 60, 70, 0.55);
    --button-light: #f2f3f5;
    --button-mid: #b9bcc2;
    --button-dark: #6f737b;
    --button-ink: #2b2d31;
    --jacket-navy: #1f3657;
    --hair-gold: #a7754a;
    --knit-grey: #bdbdbd;
  }
  html, body {
    margin: 0;
    padding: 0;
    overflow: hidden;
  }
  .banner {
    position: relative;
    width: 1200px;
    height: 627px;
    overflow: hidden;
    background: var(--centre-white);
    font-family: "Open Sans", sans-serif;
  }
  .backdrop {
    position: absolute;
    inset: 0;
    background:
      radial-gradient(ellipse 48% 70% at 52% 45%, var(--centre-white) 0%, var(--mist) 55%, rgba(223,225,234,0) 80%),
      linear-gradient(90deg, var(--edge-blue) 0%, var(--edge-lavender) 22%, var(--mist) 45%, var(--mist) 62%, var(--edge-lavender) 85%, var(--edge-blue) 100%);
  }
  .title-band {
    position: absolute;
    left: 330px;
    top: 253px;
    width: 870px;
    height: 62px;
    background: linear-gradient(180deg, #ffffff 0%, var(--band) 100%);
    box-shadow: 0 3px 6px rgba(0,0,0,0.18), 0 -2px 4px rgba(0,0,0,0.08);
  }
  .model-photo {
    position: absolute;
    left: 45px;
    top: 25px;
    width: 300px;
    height: 602px;
    background: linear-gradient(180deg, var(--hair-gold) 0%, var(--hair-gold) 22%, var(--jacket-navy) 35%, var(--jacket-navy) 76%, var(--knit-grey) 80%, var(--knit-grey) 92%, #111 96%);
    border-radius: 120px 120px 0 0;
  }
  .headline {
    position: absolute;
    left: 800px;
    top: 180px;
    width: 336px;
    text-align: center;
    margin: 0;
    font-weight: normal;
  }
  .headline .script {
    display: block;
    font-family: "Cookie", cursive;
    color: var(--script-white);
    text-shadow: 1px 2px 2px var(--script-shadow);
    line-height: 1;
  }
  .headline .script-new {
    font-size: 62px;
    margin-left: -12px;
  }
  .headline .season {
    display: block;
    font-family: "Cinzel", serif;
    font-weight: 700;
    font-size: 52px;
    color: var(--ink);
    line-height: 1;
    margin-top: 6px;
    margin-left: 12px;
  }
  .headline .script-collection {
    font-size: 70px;
    margin-top: 2px;
    margin-left: 36px;
  }
  .shop-button {
    position: absolute;
    left: 812px;
    top: 460px;
    width: 303px;
    height: 45px;
    border-radius: 23px;
    background: linear-gradient(180deg, var(--button-light) 0%, #d8dadf 45%, var(--button-mid) 55%, var(--button-dark) 100%);
    box-shadow: 0 2px 4px rgba(0,0,0,0.35);
    display: flex;
    align-items: center;
    justify-content: center;
    font-size: 23px;
    color: var(--button-ink);
    letter-spacing: 0.3px;
    text-decoration: none;
  }
  .shop-button b { font-weight: 700; }
  .shop-button span { font-weight: 400; margin: 0 6px; }
</style>
</head>
<body>
  <div class="banner">
    <div class="backdrop" role="img" aria-label="Soft winter backdrop of blue snowflakes and sparkles fading to white in the centre"></div>
    <div class="title-band"></div>
    <div class="model-photo" role="img" aria-label="Photo of a woman with long wavy hair wearing a navy quilted jacket with fur collar and grey knit hem"></div>
    <h1 class="headline">
      <span class="script script-new">New</span>
      <span class="season">WINTER</span>
      <span class="script script-collection">Collection</span>
    </h1>
    <a class="shop-button" href="#"><b>SHOP</b><span>THE</span><b>SEASON</b></a>
  </div>
</body>
</html>
```